High end Electrical/home automation Business Card

Need a card for a high end electrical and home automation company utilising the existing logo.
Phone
Email
Website

Like black look with raised detail. Don’t necessarily need to keep colour of logo it could be made grayscale or white etc

Target Market(s)

High end clients

Contact Information for Business Card

Brightmoor Electrical

Requirements
Must have
• Logo, phone, email, website, address

High end look
Nice to have
• Black background card
Raised font
Should not have
• Lots of colour

```html
<!DOCTYPE html>
<html lang="en">
<head>
<meta charset="utf-8">
<title>Brightmoor Electrical — Business Card</title>
<link rel="stylesheet" href="https://fonts.googleapis.com/css2?family=Arimo:wght@400;700&display=swap">
<style>
  :root {
    --backdrop: #2c2c2c;
    --card: #232323;
    --card-edge: #2a2a2a;
    --accent: #2496d8;
    --ink: #ffffff;
    --ink-soft: #e6e6e6;
  }
  * { box-sizing: border-box; margin: 0; padding: 0; }
  html, body { width: 1200px; height: 900px; overflow: hidden; }
  body {
    background: var(--backdrop);
    font-family: "Arimo", Arial, sans-serif;
    color: var(--ink);
    display: flex;
    flex-direction: column;
    align-items: center;
    justify-content: center;
    gap: 44px;
  }
  .card {
    position: relative;
    width: 640px;
    height: 366px;
    background: linear-gradient(135deg, var(--card) 0%, var(--card-edge) 100%);
    box-shadow: 0 10px 24px rgba(0,0,0,.55);
    overflow: hidden;
  }
  .card__band {
    position: absolute;
    left: 0; right: 0; bottom: 0;
    height: 14px;
    background: var(--accent);
  }
  /* Front */
  .card--front {
    display: flex;
    align-items: center;
    justify-content: center;
  }
  .wordmark {
    display: flex;
    align-items: center;
    gap: 14px;
    font-weight: 700;
    color: var(--ink);
    letter-spacing: -0.5px;
    margin-bottom: 40px;
  }
  .wordmark__dot {
    width: 20px; height: 20px;
    border-radius: 50%;
    background: var(--accent);
  }
  .card--front .wordmark { font-size: 38px; }
  /* Back */
  .card--back {
    display: grid;
    grid-template-columns: 300px 1fr;
    align-items: center;
    padding-bottom: 30px;
  }
  .brand-side {
    display: flex;
    justify-content: center;
  }
  .brand-side .wordmark { font-size: 25px; margin: 0; gap: 10px; }
  .brand-side .wordmark__dot { width: 14px; height: 14px; }
  .divider {
    position: absolute;
    left: 300px;
    top: 60px;
    width: 1px;
    height: 220px;
    background: linear-gradient(to bottom, transparent, var(--accent), transparent);
  }
  .contact { padding-left: 28px; }
  .contact__name {
    font-size: 27px;
    font-weight: 700;
    color: var(--accent);
    line-height: 1;
  }
  .contact__role {
    font-size: 15px;
    color: var(--ink-soft);
    margin: 4px 0 20px;
  }
  .contact__list { list-style: none; }
  .contact__item {
    display: flex;
    align-items: flex-start;
    gap: 9px;
    font-size: 15px;
    line-height: 1.3;
    margin-bottom: 5px;
    color: var(--ink);
  }
  .contact__icon {
    flex: none;
    width: 13px; height: 13px;
    margin-top: 3px;
    fill: var(--accent);
  }
  .contact__highlight { color: var(--accent); }
</style>
</head>
<body>

  <section class="card card--front" aria-label="Card front">
    <div class="wordmark"><span class="wordmark__dot"></span>Brightmoor Electrical</div>
    <div class="card__band"></div>
  </section>

  <section class="card card--back" aria-label="Card back">
    <div class="brand-side">
      <div class="wordmark"><span class="wordmark__dot"></span>Brightmoor Electrical</div>
    </div>
    <div class="divider"></div>
    <div class="contact">
      <div class="contact__name">Dorian Hale</div>
      <div class="contact__role">Co-Founder</div>
      <ul class="contact__list">
        <li class="contact__item">
          <svg class="contact__icon" viewBox="0 0 24 24" aria-hidden="true"><path d="M6.6 10.8a15.1 15.1 0 0 0 6.6 6.6l2.2-2.2c.3-.3.7-.4 1-.2 1.1.4 2.3.6 3.6.6.6 0 1 .4 1 1V20c0 .6-.4 1-1 1A17 17 0 0 1 3 4c0-.6.4-1 1-1h3.5c.6 0 1 .4 1 1 0 1.3.2 2.5.6 3.6.1.3 0 .7-.2 1z"/></svg>
          123-555-0147
        </li>
        <li class="contact__item">
          <svg class="contact__icon" viewBox="0 0 24 24" aria-hidden="true"><path d="M2 5h20v14H2z M2 5l10 8 10-8" fill="none" stroke="#2496d8" stroke-width="2"/></svg>
          dorian@brightmoorelectrical.com
        </li>
        <li class="contact__item">
          <svg class="contact__icon" viewBox="0 0 24 24" aria-hidden="true"><circle cx="12" cy="12" r="9" fill="none" stroke="#2496d8" stroke-width="2"/><path d="M3 12h18M12 3c3 3 3 15 0 18M12 3c-3 3-3 15 0 18" fill="none" stroke="#2496d8" stroke-width="1.6"/></svg>
          <span>www.<span class="contact__highlight">brightmoorelectrical</span>.com</span>
        </li>
        <li class="contact__item">
          <svg class="contact__icon" viewBox="0 0 24 24" aria-hidden="true"><path d="M12 2a7 7 0 0 0-7 7c0 5 7 13 7 13s7-8 7-13a7 7 0 0 0-7-7zm0 9.5a2.5 2.5 0 1 1 0-5 2.5 2.5 0 0 1 0 5z"/></svg>
          <span>4120 Larkspur Valley Rd<br>Suite C Fairview, OH 45099</span>
        </li>
      </ul>
    </div>
    <div class="card__band"></div>
  </section>

</body>
</html>
```